KVM Contracting services . Building and maintenance services, optic fibre installation

Business cards and logo design.I need a logo that I can use on business cards ,workwear and on my vehicles. I would like the KVM to be the main or larger text and contracting services to be the smaller or less important text.I like monograms, modern designs and repeating patterns symbols. I am also a Gemini and my favourite number is 22 so if this can be any inspiration to help with the design. Am thinking of the using German flag colours as a his is my family’s heritage. And the other 2 main colours I wear is black and white.But any ideas are appreciated.I do not need a design that is trade specific but a design that could be used for any business.

Target Market(s)

General public

Contact Information for Business Card

KVM Contracting Services ( front of business card)

(Back of business card)
Darren Holtwick
0451907326
Maintenance services
Optic fibre and data installation

Logo Text

Logo can just be pattern or monogram or incorporate KVM . I like the gemini star sign and the number 22

Colors
ec1f27
000000
fbee3e
ffffff

Requirements
Must have
• Logo and KVM Contracting Services on the front of business card
Nice to have
• Possible use of German flag colours.
• Modern design.
• Design to be able to be used on black or white background as I want to put it on clothing

```html
<!DOCTYPE html>
<html lang="en">
<head>
<meta charset="utf-8">
<title>KVM Contracting Services – Business Cards</title>
<link href="https://fonts.googleapis.com/css2?family=Open+Sans:wght@400;700;800&display=swap" rel="stylesheet">
<style>
  :root {
    --backdrop: #141414;
    --card: #1e1e1e;
    --red: #ec1f27;
    --white: #ffffff;
    --text-light: #e6e6e6;
    --rule: #5a5a5a;
  }
  * { box-sizing: border-box; margin: 0; padding: 0; }
  html, body {
    width: 1200px;
    height: 900px;
    overflow: hidden;
    background: var(--backdrop);
    font-family: "Open Sans", Arial, sans-serif;
  }
  .stage {
    width: 1200px;
    height: 900px;
    display: flex;
    flex-direction: column;
    align-items: center;
    justify-content: center;
    gap: 44px;
  }
  .card {
    width: 595px;
    height: 340px;
    background: var(--card);
    border-radius: 22px;
    box-shadow: 0 18px 40px rgba(0, 0, 0, 0.55);
    display: flex;
    flex-direction: column;
    align-items: center;
    justify-content: center;
    text-align: center;
  }
  /* Front */
  .brand {
    display: flex;
    align-items: center;
    gap: 18px;
    color: var(--red);
    font-weight: 800;
  }
  .brand-dot {
    width: 64px;
    height: 64px;
    border-radius: 50%;
    background: var(--red);
  }
  .brand-name {
    display: flex;
    flex-direction: column;
    align-items: flex-start;
    line-height: 1;
  }
  .brand-initials {
    font-size: 78px;
    letter-spacing: 4px;
  }
  .brand-tagline {
    font-size: 13.5px;
    letter-spacing: 0.5px;
    text-transform: uppercase;
    margin-top: 2px;
  }
  /* Back */
  .contact-name {
    color: var(--red);
    font-weight: 700;
    font-size: 24px;
    letter-spacing: 0.5px;
    text-transform: uppercase;
  }
  .contact-phone {
    color: var(--white);
    font-size: 25px;
    letter-spacing: 1px;
    margin-top: 2px;
  }
  .divider {
    width: 220px;
    height: 1px;
    background: var(--rule);
    margin: 18px 0 16px;
  }
  .services {
    list-style: none;
    color: var(--text-light);
    font-size: 18px;
    line-height: 1.3;
    text-transform: uppercase;
    letter-spacing: 0.3px;
  }
</style>
</head>
<body>
  <main class="stage">
    <section class="card card-front" aria-label="Business card front">
      <div class="brand">
        <span class="brand-dot" aria-hidden="true"></span>
        <div class="brand-name">
          <span class="brand-initials">KVM</span>
          <span class="brand-tagline">Contracting Services</span>
        </div>
      </div>
    </section>

    <section class="card card-back" aria-label="Business card back">
      <p class="contact-name">Darren Holtwick</p>
      <p class="contact-phone">0451907326</p>
      <div class="divider"></div>
      <ul class="services">
        <li>Maintenance Services</li>
        <li>Optic Fibre and Data Installation</li>
      </ul>
    </section>
  </main>
</body>
</html>
```